Business card

We need a business card design for our company based in Auckland , New Zealand called 'Ridge + Studio Ltd'. We provide architectural services. We would like to see designs that use the max. three colours (such as white, black, grey) The final design should communicate financial safety and growth."
Also I will provide our company logo. I would like to the logo to be embeded onto our business card.

Target Market(s)

new residential house, alteration & addition & light commericila design & drafting service

Industry/Entity Type

Architecture

Contact Information for Business Card

Company name: ridge + studio Ltd.
Name: Mark Delford
Job title: architectural designer & Design LBP
email address: mark@rplusd.co.nz
mobile number: 02 5163 2290
web site: www.rplusd.co.nz

Requirements
Must have
• My project must have..
• - embeded logo (attached company logo)
• I don't have a bigger version for our company logo, but I have one old one, so you can remove the word from it)
• - insert the attached small BKTW logo & LBP logo
• - creative, simple and clear business card.
• - Max. three colours
Nice to have
• - Here are the samples I would like to share with you: http://www.plimvora.com/blog/minimalistic-business-card-designs/
• I would like to have my business card like one of the creation.
Should not have
• TBA

```html
<!DOCTYPE html>
<html lang="en">
<head>
<meta charset="utf-8">
<title>Ridge + Studio Ltd — Business Card</title>
<link href="https://fonts.googleapis.com/css2?family=Montserrat:wght@400;600;700&display=swap" rel="stylesheet">
<style>
  :root {
    --bg: #2a2a2a;
    --card: #050505;
    --white: #ffffff;
    --grey: #8a8a8a;
    --faint: #2b2b2b;
  }
  * { margin: 0; padding: 0; box-sizing: border-box; }
  html, body { width: 1200px; height: 900px; overflow: hidden; }
  body {
    background: var(--bg);
    font-family: "Montserrat", Arial, sans-serif;
    color: var(--white);
    display: flex;
    flex-direction: column;
    align-items: center;
    justify-content: center;
    gap: 40px;
  }
  .card {
    position: relative;
    width: 700px;
    height: 400px;
    background: var(--card);
    border-radius: 28px;
    overflow: hidden;
  }
  .brand-mark {
    position: absolute;
    border: 3px solid var(--white);
    border-radius: 50%;
  }
  .brand-name {
    position: absolute;
    font-weight: 600;
    font-size: 26px;
    letter-spacing: 0.2px;
    white-space: nowrap;
    color: var(--white);
  }

  /* front */
  .front .brand-mark { left: 70px; top: 60px; width: 130px; height: 130px; }
  .front .brand-name { left: 70px; top: 220px; }
  .front .credentials {
    position: absolute; right: 50px; top: 150px;
    display: flex; align-items: flex-start; gap: 30px;
  }
  .member-badge { width: 70px; height: 70px; background: var(--grey); }
  .licence-badge { width: 90px; height: 90px; border-radius: 50%; background: var(--white); }
  .front .site {
    position: absolute; right: 50px; bottom: 70px;
    font-size: 22px; font-weight: 400;
  }

  /* back */
  .back .side-band {
    position: absolute; left: 0; top: 0; bottom: 0; width: 72px;
    background: var(--white);
  }
  .back .side-rule {
    position: absolute; left: 80px; top: 0; bottom: 0; width: 4px;
    background: var(--white);
  }
  .back .brand-mark {
    left: 36px; top: 60px; width: 130px; height: 130px;
    background: var(--card);
  }
  .back .brand-name { left: 190px; top: 95px; font-size: 25px; }
  .back .deco-ring {
    position: absolute; right: -30px; top: -40px;
    width: 330px; height: 330px; border-radius: 50%;
    border: 8px solid var(--faint);
  }
  .person { position: absolute; left: 300px; top: 175px; }
  .person-name { font-size: 30px; font-weight: 700; letter-spacing: 1px; }
  .person-title { font-size: 17px; line-height: 1.25; margin-top: 4px; }
  .contacts { list-style: none; margin-top: 12px; }
  .contacts li {
    display: flex; align-items: center; gap: 12px;
    font-size: 17px; line-height: 1.5;
  }
  .contacts svg { width: 16px; height: 16px; fill: none; stroke: var(--white); stroke-width: 1.8; }
</style>
</head>
<body>

<section class="card front">
  <div class="brand-mark"></div>
  <div class="brand-name">Ridge + Studio Ltd</div>
  <div class="credentials">
    <div class="member-badge" role="img" aria-label="Professional membership badge"></div>
    <div class="licence-badge" role="img" aria-label="Licensed practitioner badge"></div>
  </div>
  <div class="site">www.rplusd.co.nz</div>
</section>

<section class="card back">
  <div class="deco-ring"></div>
  <div class="side-band"></div>
  <div class="side-rule"></div>
  <div class="brand-mark"></div>
  <div class="brand-name">Ridge + Studio Ltd</div>
  <div class="person">
    <div class="person-name">MARK DELFORD</div>
    <div class="person-title">Architectural designer<br>&amp; Design LBP</div>
    <ul class="contacts">
      <li><svg viewBox="0 0 16 16"><path d="M3 2l3 1 1 3-2 1a8 8 0 004 4l1-2 3 1 1 3-2 1C7 14 2 9 2 4z"/></svg>02 5163 2290</li>
      <li><svg viewBox="0 0 16 16"><rect x="1.5" y="3.5" width="13" height="9"/><path d="M1.5 3.5l6.5 5 6.5-5"/></svg>mark@rplusd.co.nz</li>
      <li><svg viewBox="0 0 16 16"><circle cx="8" cy="8" r="6.5"/><path d="M1.5 8h13M8 1.5c-3 3.5-3 9.5 0 13M8 1.5c3 3.5 3 9.5 0 13"/></svg>www.rplusd.co.nz</li>
    </ul>
  </div>
</section>

</body>
</html>
```